Working Capital graphics

Our business advisory firm requires 9 images to be re-created and improved in the branding of our business.

The 9 images have been uploaded below and the colours and branding of the business can be found at the website www.tallowmereadvisory.com.au

```html
<!DOCTYPE html>
<html lang="en">
<head>
<meta charset="utf-8">
<title>Next $100 of Sales Volume – Working Capital Cycle</title>
<link rel="stylesheet" href="https://fonts.googleapis.com/css2?family=Montserrat:wght@500;700;800&family=Source+Sans+3:wght@400&display=swap">
<style>
  :root {
    --navy: #1a2a52;
    --seg-zero: #1a2a52;
    --seg-cost: #223f87;
    --seg-opex: #22509b;
    --seg-below: #1a5fa8;
    --seg-wc: #137fc2;
    --seg-debt: #2eaee2;
    --seg-cash: #68c8f1;
    --hub: #e6e7e8;
    --flag: #f6921e;
    --pole: #9a9a9a;
    --white: #ffffff;
  }
  html, body {
    margin: 0;
    padding: 0;
    width: 1200px;
    height: 1107px;
    overflow: hidden;
    background: var(--white);
  }
  .cycle-chart { display: block; width: 1200px; height: 1107px; }
  .segment { stroke: var(--white); stroke-width: 6; stroke-linejoin: miter; }
  .seg-zero { fill: var(--seg-zero); }
  .seg-cost { fill: var(--seg-cost); }
  .seg-opex { fill: var(--seg-opex); }
  .seg-below { fill: var(--seg-below); }
  .seg-wc { fill: var(--seg-wc); }
  .seg-debt { fill: var(--seg-debt); }
  .seg-cash { fill: var(--seg-cash); }
  .hub { fill: var(--hub); stroke: var(--white); stroke-width: 8; }
  .title, .hub-label, .seg-label, .zero-label {
    font-family: "Montserrat", Arial, sans-serif;
  }
  .title { font-size: 38px; font-weight: 700; fill: var(--navy); letter-spacing: 1px; }
  .hub-label { font-size: 66px; font-weight: 800; fill: var(--navy); }
  .zero-label { font-size: 62px; font-weight: 700; fill: var(--white); }
  .seg-label { fill: var(--white); font-weight: 500; letter-spacing: 1px; }
  .seg-label.lg { font-size: 32px; }
  .seg-label.md { font-size: 24px; }
  .seg-label.sm { font-size: 20px; }
  .flag-shape { fill: var(--flag); }
  .flag-pole { fill: var(--pole); }
  .flag-label {
    font-family: "Source Sans 3", Arial, sans-serif;
    font-size: 18px;
    fill: var(--white);
  }
</style>
</head>
<body>
<svg class="cycle-chart" viewBox="0 0 1414 1304" xmlns="http://www.w3.org/2000/svg">
  <defs>
    <path id="arc-cost" d="M750,241.3 A345,345 0 0 1 1000.8,410.5"/>
  </defs>

  <text class="title" x="702" y="122" text-anchor="middle">REVENUE $0</text>

  <g class="ring">
    <path class="segment seg-cost" d="M702,146 A437,437 0 0 1 1072.6,351.4 L1019.2,435.1 L924.2,444.2 A262,262 0 0 0 702,321 L744.7,235.6 Z"/>
    <path class="segment seg-opex" d="M1072.6,351.4 A437,437 0 0 1 1087.8,788.2 L988.7,783.8 L933.3,706 A262,262 0 0 0 924.2,444.2 L1019.2,435.1 Z"/>
    <path class="segment seg-below" d="M1087.8,788.2 A437,437 0 0 1 717.3,1019.7 L671.5,931.7 L711.1,844.8 A262,262 0 0 0 933.3,706 L988.7,783.8 Z"/>
    <path class="segment seg-wc" d="M717.3,1019.7 A437,437 0 0 1 323.6,801.5 L379.8,719.7 L475.1,714 A262,262 0 0 0 711.1,844.8 L671.5,931.7 Z"/>
    <path class="segment seg-debt" d="M323.6,801.5 A437,437 0 0 1 331.4,351.4 L430,362.7 L479.8,444.2 A262,262 0 0 0 475.1,714 L379.8,719.7 Z"/>
    <path class="segment seg-cash" d="M331.4,351.4 A437,437 0 0 1 496.8,197.2 L576.6,256.2 L579,351.7 A262,262 0 0 0 479.8,444.2 L430,362.7 Z"/>
    <path class="segment seg-zero" d="M496.8,197.2 A437,437 0 0 1 702,146 L744.7,235.6 L702,321 A262,262 0 0 0 579,351.7 L576.6,256.2 Z"/>
    <circle class="hub" cx="702" cy="583" r="272"/>
  </g>

  <text class="zero-label" x="655" y="248" text-anchor="middle">$0</text>

  <text class="seg-label lg"><textPath href="#arc-cost" startOffset="50%" text-anchor="middle">COST OF SALES</textPath></text>

  <g class="seg-label md">
    <text transform="translate(1030,555) rotate(90)" text-anchor="middle">OPERATING</text>
    <text transform="translate(1056,555) rotate(90)" text-anchor="middle" dy="0">EXPENSES</text>
    <text transform="translate(1036,705) rotate(100)" text-anchor="middle">FIXED</text>
    <text transform="translate(1010,700) rotate(100)" text-anchor="middle">COSTS</text>
  </g>

  <g class="seg-label sm">
    <text transform="translate(962,840) rotate(-35)" text-anchor="middle">TAX</text>
    <text transform="translate(882,895) rotate(-20)" text-anchor="middle">INTEREST</text>
    <text transform="translate(752,940) rotate(-7)" text-anchor="middle">DIVIDENTS</text>
  </g>

  <g class="seg-label lg">
    <text transform="translate(415,795) rotate(32)" text-anchor="middle">AR</text>
    <text transform="translate(405,830) rotate(32)" text-anchor="middle">DAYS</text>
    <text transform="translate(518,868) rotate(24)" text-anchor="middle">AP</text>
    <text transform="translate(495,903) rotate(24)" text-anchor="middle">DAYS</text>
    <text transform="translate(600,908) rotate(14)" text-anchor="middle">INV</text>
    <text transform="translate(595,945) rotate(14)" text-anchor="middle">DAYS</text>
    <text transform="translate(378,540) rotate(-78)" text-anchor="middle">ADDITIONAL DEBT</text>
  </g>

  <g class="seg-label md">
    <text transform="translate(488,297) rotate(-38)" text-anchor="middle">CASH</text>
    <text transform="translate(510,323) rotate(-38)" text-anchor="middle">SHORTFALL</text>
  </g>

  <g class="hub-label" text-anchor="middle">
    <text x="702" y="538">NEXT $100</text>
    <text x="702" y="603">OF SALES</text>
    <text x="702" y="668">VOLUME</text>
  </g>

  <g class="flag flag-funding">
    <rect class="flag-pole" x="88" y="303" width="8" height="165"/>
    <polygon class="flag-shape" points="102,303 262,303 238,358 262,413 102,413"/>
    <text class="flag-label" text-anchor="middle"><tspan x="170" y="336">AFTER</tspan><tspan x="170" y="355">ADDITIONAL</tspan><tspan x="170" y="374">FUNDING</tspan><tspan x="170" y="393">$0</tspan></text>
  </g>
  <g class="flag flag-working-capital">
    <rect class="flag-pole" x="88" y="735" width="8" height="165"/>
    <polygon class="flag-shape" points="102,735 262,735 238,790 262,845 102,845"/>
    <text class="flag-label" text-anchor="middle"><tspan x="170" y="768">AFTER</tspan><tspan x="170" y="787">WORKING</tspan><tspan x="170" y="806">CAPITAL</tspan><tspan x="170" y="825">$0</tspan></text>
  </g>
  <g class="flag flag-gross-margin">
    <rect class="flag-pole" x="1161" y="303" width="8" height="165"/>
    <polygon class="flag-shape" points="1173,303 1334,303 1310,358 1334,413 1173,413"/>
    <text class="flag-label" text-anchor="middle"><tspan x="1242" y="345">GROSS</tspan><tspan x="1242" y="364">MARGIN</tspan><tspan x="1242" y="383">$0</tspan></text>
  </g>
  <g class="flag flag-ebit">
    <rect class="flag-pole" x="1161" y="735" width="8" height="165"/>
    <polygon class="flag-shape" points="1173,735 1334,735 1310,790 1334,845 1173,845"/>
    <text class="flag-label" text-anchor="middle"><tspan x="1242" y="786">EBIT</tspan><tspan x="1242" y="805">$0</tspan></text>
  </g>
  <g class="flag flag-retained">
    <rect class="flag-pole" x="616" y="1057" width="8" height="165"/>
    <polygon class="flag-shape" points="628,1057 789,1057 765,1112 789,1167 628,1167"/>
    <text class="flag-label" text-anchor="middle"><tspan x="697" y="1099">RETAINED</tspan><tspan x="697" y="1118">INCOME</tspan><tspan x="697" y="1137">$0</tspan></text>
  </g>
</svg>
</body>
</html>
```